Craft Beer Company

We need a web design for our Tampa based craft beer company that shows and tells what we are about and our products, up and coming beers, events and happenings. Must has a verify age by selecting yes or no to "are you 21 years or older.. have logos and product labels etc... currently have Plimtora.com a our website, thats under construction.
Reason: more time to be thorough
Target Market(s)
Craft Beer Enthusiasts , Craft Beer Community
Industry/Entity Type
Construction
Requirements
Must have
- The pages on the site should have, about us, events, our beer, store for e-commerce
being that we are set up with Plimtora.com I would like to contineu to use them, unless there is another option available. We have the domain there.

```html
<!DOCTYPE html>
<html lang="en">
<head>
<meta charset="utf-8">
<title>Harborline Beer Company</title>
<link rel="stylesheet" href="https://fonts.googleapis.com/css2?family=Alegreya:ital,wght@0,400;1,400&family=Roboto:wght@400&display=swap">
<style>
:root{
  --nav-bg:#1a1a1a;
  --nav-text:#8fbf4a;
  --nav-active:#5e9a2c;
  --nav-active-text:#e6e6e6;
  --hero-text:#dcdcdc;
  --badge-ring:#b5b5b5;
  --badge-text:#3a3a3a;
  --shade:rgba(0,0,0,0.52);
  --white:#ffffff;
  --yes:#6fa83a;
  --no:#000000;
}
*{margin:0;padding:0;box-sizing:border-box}
html,body{width:1200px;height:798px;overflow:hidden;background:#000}
.page{position:relative;width:1200px;height:798px;overflow:hidden;font-family:"Alegreya",serif}
.site-nav{position:absolute;left:0;top:0;width:1200px;height:109px;background:var(--nav-bg)}
.brand{position:absolute;left:48px;top:0;height:109px;display:flex;align-items:center;gap:8px;color:var(--nav-text);font-family:"Alegreya",serif;font-size:19px;line-height:1.1}
.brand-dot{width:18px;height:18px;border-radius:50%;background:var(--nav-text)}
.menu{position:absolute;left:222px;top:0;height:109px;display:flex;list-style:none;font-family:"Roboto",sans-serif;font-size:16px}
.menu li{height:109px;display:flex;align-items:center;color:var(--nav-text)}
.menu .active{background:var(--nav-active);color:var(--nav-active-text);width:103px;justify-content:center;border-left:3px solid #2c2c2c;border-right:3px solid #2c2c2c}
.menu li+li{margin-left:57px}
.menu .active+li{margin-left:31px}
.hero{position:absolute;left:0;top:109px;width:1200px;height:689px}
.hero-photo{position:absolute;inset:0;background:
  radial-gradient(ellipse 60% 55% at 50% 50%,#c99a2e 0%,#8f6a24 45%,transparent 75%),
  linear-gradient(180deg,#d9d2c2 0%,#c8bda6 35%,#8a6a33 70%,#3d2a14 100%)}
.hero-copy{position:absolute;left:0;width:1200px;text-align:center;color:var(--hero-text)}
.hero-welcome{top:205px;font-size:51px}
.hero-title{top:272px;font-size:65px}
.hero-sub{top:335px;font-size:40px;font-style:italic}
.slide-arrow{position:absolute;width:22px;height:34px}
.badge{position:absolute;left:967px;top:130px;width:156px;height:156px;border:8px solid var(--badge-ring);border-radius:50%;display:flex;align-items:center;justify-content:center;text-align:center;color:var(--badge-text);font-size:22px;line-height:1.25}
.shade{position:absolute;inset:0;background:var(--shade)}
.age-gate{position:absolute;left:247px;top:298px;width:706px;height:201px;border:1px solid var(--white);text-align:center}
.age-question{margin-top:42px;color:var(--white);font-size:34px;line-height:1}
.age-actions{position:absolute;left:214px;top:108px;display:flex;gap:56px}
.age-btn{width:111px;height:44px;display:flex;align-items:center;justify-content:center;font-size:30px;color:var(--white)}
.age-btn.yes{background:var(--yes)}
.age-btn.no{background:var(--no)}
.close{position:absolute;left:946px;top:278px;width:29px;height:29px}
</style>
</head>
<body>
<div class="page">
  <header class="site-nav">
    <div class="brand"><span class="brand-dot"></span><span>Harborline<br>Beer Co.</span></div>
    <ul class="menu">
      <li class="active">Home</li>
      <li>About Us</li>
      <li>Upcoming Beers</li>
      <li>Events &amp; Happenings</li>
      <li>Our History</li>
      <li>Contact Us</li>
    </ul>
  </header>

  <section class="hero">
    <div class="hero-photo" role="img" aria-label="Row of assorted craft beer glasses filled with golden and amber beer on a wooden bar"></div>
    <p class="hero-copy hero-welcome">Welcome</p>
    <p class="hero-copy hero-title">Lorem ipsum dolor sit amet</p>
    <p class="hero-copy hero-sub">Consectetuer Adipiscingtelit Pellentesque Sed dvolor.</p>
    <svg class="slide-arrow" style="left:58px;top:314px" viewBox="0 0 22 34"><path d="M18 3 L5 17 L18 31" fill="none" stroke="#e0e0e0" stroke-width="3"/></svg>
    <svg class="slide-arrow" style="left:1121px;top:324px" viewBox="0 0 22 34"><path d="M4 3 L17 17 L4 31" fill="none" stroke="#e0e0e0" stroke-width="3"/></svg>
  </section>

  <div class="badge">Harborline<br>Beer<br>Company</div>

  <div class="shade"></div>

  <div class="age-gate">
    <p class="age-question">Are you 21 years or older?</p>
    <div class="age-actions">
      <span class="age-btn yes">yes</span>
      <span class="age-btn no">No</span>
    </div>
  </div>
  <svg class="close" viewBox="0 0 30 30" aria-label="Close">
    <circle cx="15" cy="15" r="15" fill="#ffffff"/>
    <path d="M10 10 L20 20 M20 10 L10 20" stroke="#111" stroke-width="3.2" stroke-linecap="round"/>
  </svg>
</div>
</body>
</html>
```